Business Cards for a law firm

Business cards for our law firm. Use our silhoette logo and OAK PARTNERS - check our website (www.oakpartners.example)

Contact Information for Business Card

our silhouette logo, OAK PARTNERS, 800-555-0147, Dorian Pemberton, dorian@oakpartners.example

Requirements
Must have
• our silhouette logo, OAK PARTNERS, 800-555-0147, Dorian Pemberton, dorian@oakpartners.example

```html
<!DOCTYPE html>
<html lang="en">
<head>
<meta charset="utf-8">
<title>Oak Partners Business Cards</title>
<link rel="stylesheet" href="https://fonts.googleapis.com/css2?family=Cinzel:wght@600&family=Arimo:wght@400&display=swap">
<style>
  :root {
    --stage: #3d3d3d;
    --navy: #1b3169;
    --navy-soft: #2a4585;
    --paper: #ffffff;
    --ink-grey: #555b66;
    --light-text: #e8ecf5;
  }
  * { margin: 0; padding: 0; box-sizing: border-box; }
  html, body { width: 1200px; height: 803px; overflow: hidden; }
  body { background: var(--stage); position: relative; }

  .card {
    position: absolute;
    top: 247px;
    width: 540px;
    height: 309px;
    border-radius: 26px;
    overflow: hidden;
  }
  .card--front { left: 40px; background: var(--paper); }
  .card--back { left: 620px; background: var(--navy); }

  .figure-art {
    position: absolute;
    right: 0; top: 0;
    width: 250px; height: 285px;
    background: linear-gradient(160deg, var(--navy-soft), var(--navy));
    border-bottom-left-radius: 40px;
  }

  .brand {
    position: absolute;
    left: 34px; top: 92px;
    display: flex; align-items: center; gap: 10px;
  }
  .brand__mark { width: 18px; height: 18px; background: var(--navy); }
  .brand__name {
    font-family: "Cinzel", serif;
    font-weight: 600;
    font-size: 22px;
    letter-spacing: 1px;
    color: var(--navy);
  }

  .person {
    position: absolute;
    left: 34px; top: 168px;
    font-family: "Cinzel", serif;
    font-weight: 600;
    font-size: 17px;
    letter-spacing: 0.5px;
    color: var(--navy);
  }

  .contacts {
    position: absolute;
    left: 34px; top: 202px;
    list-style: none;
    font-family: "Arimo", sans-serif;
    font-size: 13px;
    color: var(--ink-grey);
    line-height: 19px;
  }
  .contacts li { display: flex; align-items: center; gap: 8px; }
  .contacts svg { width: 11px; height: 11px; fill: var(--navy); flex: none; }

  .back-brand {
    position: absolute;
    left: 0; right: 0; top: 118px;
    text-align: center;
    font-family: "Cinzel", serif;
    font-weight: 600;
    font-size: 26px;
    letter-spacing: 2px;
    color: var(--navy-soft);
  }
  .back-url {
    position: absolute;
    left: 0; right: 0; bottom: 46px;
    text-align: center;
    font-family: "Arimo", sans-serif;
    font-size: 15px;
    color: var(--light-text);
  }
</style>
</head>
<body>
  <section class="card card--front">
    <div class="figure-art" role="img" aria-label="Large silhouette artwork of two standing men in navy"></div>
    <div class="brand">
      <span class="brand__mark"></span>
      <span class="brand__name">OAK PARTNERS</span>
    </div>
    <p class="person">Dorian Pemberton</p>
    <ul class="contacts">
      <li><svg viewBox="0 0 10 10"><path d="M2 0h2l1 2.5-1.3 1a5 5 0 0 0 2.8 2.8l1-1.3L10 6v2a2 2 0 0 1-2 2A8 8 0 0 1 0 2a2 2 0 0 1 2-2z"/></svg>800-555-0147</li>
      <li><svg viewBox="0 0 10 10"><path d="M0 2h10v6H0z M0 2l5 3.5L10 2" stroke="#fff" stroke-width="0.8"/></svg>dorian@oakpartners.example</li>
      <li><svg viewBox="0 0 10 10"><circle cx="5" cy="5" r="5"/></svg>www.oakpartners.example</li>
    </ul>
  </section>

  <section class="card card--back">
    <p class="back-brand">OAK PARTNERS</p>
    <p class="back-url">www.oakpartners.example</p>
  </section>
</body>
</html>
```